Brightwave Reach - Business Card

We need a business card for a Social Media Marketing company that specializes in online marketing for small businesses in Canada using common Social Media platforms such as Pixlora, Chatterly, Blinkpost & Quibber.

I have uploaded a copy of our logo which I would like utilized in the business card. We would like the business card to be modern yet classy design.

Our website is www.brightwavereach.ca

Industry/Entity Type

Marketing

Contact Information for Business Card

Email: info@brightwavereach.ca
Website: www.brightwavereach.ca
Telephone: 604-555-0193

Colors

Designer to choose colors to be used in the design.

Requirements
Must have
• Social Media icons on reverse
• Please add some designs with color.

```html
<!DOCTYPE html>
<html lang="en">
<head>
<meta charset="utf-8">
<title>Brightwave Reach – Business Card</title>
<link href="https://fonts.googleapis.com/css2?family=Archivo+Black&family=Open+Sans:wght@400;600&display=swap" rel="stylesheet">
<style>
  :root {
    --backdrop: #2b2b2c;
    --card-white: #f4f4f3;
    --ink-dark: #2e3132;
    --ink-logo: #4a4c4d;
    --band-dark: #3c4143;
    --band-text: #f1f1f1;
    --rule: #3c4143;
    --accent: #1fa6b8;
    --social-1: #e4572e;
    --social-2: #3b6fd8;
    --social-3: #f2c230;
    --social-4: #29b6d9;
  }
  * { margin: 0; padding: 0; box-sizing: border-box; }
  html, body {
    width: 1200px; height: 840px; overflow: hidden;
    background: var(--backdrop);
  }
  .canvas {
    width: 1200px; height: 840px;
    display: flex; flex-direction: column;
    align-items: center; justify-content: center; gap: 50px;
  }
  .card {
    width: 600px; height: 343px;
    background: var(--card-white);
    position: relative; overflow: hidden;
    box-shadow: 0 10px 30px rgba(0,0,0,.45);
  }

  /* Logo side */
  .card--logo { display: flex; align-items: center; justify-content: center; gap: 16px; }
  .brand-mark {
    width: 26px; height: 26px;
    border: 3px solid var(--accent);
  }
  .brand-name--small {
    font-family: "Archivo Black", sans-serif;
    font-size: 30px; line-height: 1; letter-spacing: .5px;
    color: var(--ink-logo); text-transform: uppercase;
  }

  /* Contact side */
  .card--contact .card__top {
    height: 178px;
    display: flex; align-items: center; justify-content: center;
  }
  .brand-name--large {
    font-family: "Archivo Black", sans-serif;
    font-size: 44px; line-height: 1; letter-spacing: 1px;
    color: var(--ink-dark); text-transform: uppercase;
    text-align: center;
  }
  .card__rules { height: 14px; }
  .card__rules svg { display: block; }
  .card__band {
    position: absolute; left: 0; right: 0; top: 192px; bottom: 0;
    background: var(--band-dark);
    color: var(--band-text);
    font-family: "Open Sans", sans-serif;
    padding: 18px 44px 0;
  }
  .contact__name { font-size: 17px; font-weight: 600; letter-spacing: .3px; line-height: 1.3; }
  .contact__role { font-weight: 400; }
  .contact__line { font-size: 14px; margin-top: 8px; line-height: 1.3; }
  .contact__label { font-weight: 600; }
  .contact__gap { display: inline-block; width: 14px; }
  .contact__web { font-size: 14px; letter-spacing: 5px; margin-top: 8px; line-height: 1.3; }

  .social-list {
    list-style: none;
    display: flex; gap: 22px;
    margin-top: 12px;
    font-size: 13px; line-height: 1;
  }
  .social-list__item { display: flex; align-items: center; gap: 7px; }
  .social-list__dot { width: 12px; height: 12px; border-radius: 50%; }
  .social-list__dot--pixlora { background: var(--social-1); }
  .social-list__dot--chatterly { background: var(--social-2); }
  .social-list__dot--blinkpost { background: var(--social-3); }
  .social-list__dot--quibber { background: var(--social-4); }
</style>
</head>
<body>
<main class="canvas">
  <section class="card card--logo" aria-label="Business card, logo side">
    <span class="brand-mark" aria-hidden="true"></span>
    <span class="brand-name--small">Brightwave Reach</span>
  </section>

  <section class="card card--contact" aria-label="Business card, contact side">
    <div class="card__top">
      <h1 class="brand-name--large">Brightwave<br>Reach</h1>
    </div>
    <div class="card__rules">
      <svg width="600" height="14" viewBox="0 0 600 14" aria-hidden="true">
        <rect x="0" y="2" width="600" height="2" fill="var(--accent)"/>
        <rect x="0" y="8" width="600" height="4" fill="var(--rule)"/>
      </svg>
    </div>
    <div class="card__band">
      <p class="contact__name">DANIEL MARSH <span class="contact__role">- CEO/FOUNDER</span></p>
      <p class="contact__line">
        <span class="contact__label">Phone :</span> 604-555-0193<span class="contact__gap"></span>
        <span class="contact__label">Email :</span> info@brightwavereach.ca
      </p>
      <p class="contact__web">www.brightwavereach.ca</p>
      <ul class="social-list" aria-label="Social media">
        <li class="social-list__item"><span class="social-list__dot social-list__dot--pixlora"></span>Pixlora</li>
        <li class="social-list__item"><span class="social-list__dot social-list__dot--chatterly"></span>Chatterly</li>
        <li class="social-list__item"><span class="social-list__dot social-list__dot--blinkpost"></span>Blinkpost</li>
        <li class="social-list__item"><span class="social-list__dot social-list__dot--quibber"></span>Quibber</li>
      </ul>
    </div>
  </section>
</main>
</body>
</html>
```